Design NEW business card

We would like a business card using the colour deep red wine or dark navy blue textured background (patterned or not, open to suggestions) with a high gloss debossed rose gold/copper RM Roland Mercer Jewellery business name (Provided). I have included images for your review we would like to keep our currently logo and business name on the front but you can change the layout and positioning. For the back of the card we are open to all suggestions/variations.
Business
Use our current RM Roland Mercer Jewellery logo (Provided image)

```html
<!DOCTYPE html>
<html lang="en">
<head>
<meta charset="UTF-8">
<title>Roland Mercer Jewellery – Business Card</title>
<link rel="stylesheet" href="https://fonts.googleapis.com/css2?family=Montserrat:wght@300;400;600&display=swap">
<style>
  :root {
    --stage: #2a2a2c;
    --card: #121a2c;
    --card-deep: #0c1322;
    --card-edge: #1c2640;
    --texture: rgba(255, 255, 255, 0.018);
    --gold: #c49a5a;
    --gold-light: #e0bd80;
    --silver: #cfd2d8;
    --silver-soft: #9ca1ab;
    --mark-faint: rgba(255, 255, 255, 0.03);
  }
  * { box-sizing: border-box; margin: 0; padding: 0; }
  html, body {
    width: 1200px;
    height: 600px;
    overflow: hidden;
    background: var(--stage);
    font-family: "Montserrat", sans-serif;
  }
  .canvas {
    position: relative;
    width: 1200px;
    height: 600px;
    background: var(--stage);
  }
  .card {
    position: absolute;
    top: 165px;
    width: 466px;
    height: 271px;
    border-radius: 16px;
    border: 1px solid var(--card-edge);
    overflow: hidden;
    background:
      repeating-linear-gradient(45deg, var(--texture) 0 1px, transparent 1px 4px),
      repeating-linear-gradient(-45deg, var(--texture) 0 1px, transparent 1px 4px),
      radial-gradient(ellipse at 30% 25%, var(--card) 0%, var(--card-deep) 100%);
  }
  .card--front { left: 123px; }
  .card--back { left: 612px; }

  .faint-mark {
    position: absolute;
    left: 40px;
    top: 30px;
    width: 110px;
    height: 110px;
    border-radius: 50%;
    background: var(--mark-faint);
  }

  .brand {
    position: absolute;
    text-align: center;
    font-weight: 400;
    text-transform: uppercase;
    line-height: 1;
  }
  .brand__name { display: block; white-space: nowrap; }
  .brand__trade { display: block; }

  .card--front .brand {
    left: 273px;
    top: 101px;
    width: 186px;
    color: var(--gold);
  }
  .card--front .brand__name { font-size: 13px; letter-spacing: 2.4px; }
  .card--front .brand__trade { font-size: 6px; letter-spacing: 6px; margin-top: 8px; }

  .card--back .brand {
    left: 54px;
    width: 412px;
    top: 162px;
    color: var(--silver);
  }
  .card--back .brand__name { font-size: 17px; letter-spacing: 3.6px; }
  .card--back .brand__trade { font-size: 7px; letter-spacing: 9px; margin-top: 9px; }

  .holder {
    position: absolute;
    left: 40px;
    top: 152px;
    color: var(--gold-light);
  }
  .holder__name {
    font-size: 19px;
    font-weight: 300;
    letter-spacing: 0.5px;
    text-transform: uppercase;
    line-height: 1;
  }
  .holder__name strong { font-weight: 600; }
  .holder__role {
    margin-top: 8px;
    font-size: 12px;
    font-weight: 300;
    letter-spacing: 1px;
    line-height: 1;
    color: var(--gold);
  }
  .rule {
    position: absolute;
    left: 40px;
    top: 202px;
    width: 386px;
    height: 3px;
    background: linear-gradient(90deg, var(--gold), var(--gold-light), var(--gold));
  }
  .contact {
    position: absolute;
    left: 40px;
    top: 214px;
    width: 386px;
    display: flex;
    justify-content: space-between;
    align-items: center;
    font-size: 12.5px;
    font-weight: 300;
    color: var(--gold);
  }
  .contact__item { display: flex; align-items: center; gap: 6px; }
  .contact__icon { width: 13px; height: 11px; fill: var(--gold); }

  .website {
    position: absolute;
    left: 0;
    width: 474px;
    top: 217px;
    text-align: center;
    font-size: 12px;
    font-weight: 300;
    color: var(--silver-soft);
  }
</style>
</head>
<body>
<main class="canvas">
  <section class="card card--front" aria-label="Business card front">
    <div class="faint-mark" aria-hidden="true"></div>
    <div class="brand">
      <span class="brand__name">Roland Mercer</span>
      <span class="brand__trade">Jewellery</span>
    </div>
    <div class="holder">
      <p class="holder__name">Roland <strong>Mercer</strong></p>
      <p class="holder__role">OWNER</p>
    </div>
    <div class="rule"></div>
    <div class="contact">
      <span class="contact__item">
        <svg class="contact__icon" viewBox="0 0 13 11" aria-hidden="true">
          <path d="M0 3.5C0 1.5 3 0 6.5 0S13 1.5 13 3.5V4.5H9.5V3H3.5V4.5H0Z"/>
          <path d="M2 6L4 4.5H9L11 6V11H2Z"/>
        </svg>
        0000 0000 00
      </span>
      <span class="contact__item">
        youremail@xyz.com
        <svg class="contact__icon" viewBox="0 0 13 10" aria-hidden="true">
          <path d="M0 0H13V1L6.5 5.5L0 1Z"/>
          <path d="M0 2.5L6.5 7L13 2.5V10H0Z"/>
        </svg>
      </span>
    </div>
  </section>

  <section class="card card--back" aria-label="Business card back">
    <div class="faint-mark" aria-hidden="true"></div>
    <div class="brand">
      <span class="brand__name">Roland Mercer</span>
      <span class="brand__trade">Jewellery</span>
    </div>
    <p class="website">www.yourwebsite.com</p>
  </section>
</main>
</body>
</html>
```